Business Intelligence Application - Reporting Menu and Report Criteria Design

Looking for a fresh, effective and user friendly view for the menu structure and reporting criteria screen format for a business reporting application. Initial format completed, content structure is in place, but we need the 'wow' design.. as its a serious professional report/BI tool it has to fall within certain guidelines for clarity and graphics..but we want it to be slick, friendly, great user experience. There is a large amount of complex content to fit into a small space and we need it to be very inviting, modern and intuitive.. If interested, please review the attachment. We have live screens in operation, but feel these could be improved and looking forward to seeing what great creative suggestions could be made. Please review work done to date in the attached.. We are not looking for a total re-design of everything, all the basic business content/structure is there.. but tell us what we could do to improve this in terms of graphic design... particularly the criteria screens.. thanks!
Updates

Reason: Need a few more days to review designs - thanks for all submissions so far, we will make a selection shortly.

Target Market(s)

Business analysts, hotel operations teams, finance analysts hospitality industry

Industry/Entity Type

Hospitality

Coding

Coded - Design and coding required

Number of Pages Required

4 page

Font styles to use
Sans Serif
Other font styles liked:
• Candara, please see example in deck

Colors
3276b5
3176b5
0255a3
85acd3
33a6d7
cee9f5
85cae6

Requirements
Must have
• sharp clear, logical menu structure, (currently it has 'clicks to sub-menus, we need hover over, slide to sub-menus..) colour, styling.. and most focus on revision of criteria.. right now is somewhat heavy, cumbersome.. keep colour and friendly intuitive process steps.. its heavy analytical stuff.. best of luck!
Should not have
• No grey fonts on white or grey screens! many business apps are not readable or sharp.. or fonts are too small.. colourless, so please avoid that.. see our deck - sharp dark (navy) or black fonts on white, or light shading..

```html
<!DOCTYPE html>
<html lang="en">
<head>
<meta charset="utf-8">
<title>Silver Harbor Hotel &amp; Suites — Admin Menu</title>
<link href="https://fonts.googleapis.com/css2?family=Cabin:wght@400;500;600&display=swap" rel="stylesheet">
<style>
  :root {
    --navy: #0255a3;
    --sky: #33a6d7;
    --sky-line: #5cb8df;
    --ink: #0d1a2b;
    --white: #ffffff;
    --frame: #8a8f96;
  }
  * { box-sizing: border-box; margin: 0; padding: 0; }
  html, body { width: 1200px; height: 522px; overflow: hidden; background: var(--white); }
  body { font-family: "Cabin", sans-serif; color: var(--ink); position: relative; }

  .app-header {
    position: absolute; left: 0; top: 0; width: 1200px; height: 59px;
    background: var(--navy); color: var(--white);
  }
  .brand { position: absolute; left: 47px; top: 14px; display: flex; align-items: center; gap: 9px; }
  .brand-dot { width: 28px; height: 28px; border-radius: 50%; background: var(--white); }
  .brand-name { font-size: 19px; font-weight: 600; letter-spacing: -0.2px; }
  .welcome { position: absolute; left: 555px; top: 20px; font-size: 13px; }
  .today { position: absolute; left: 667px; top: 20px; font-size: 13px; }
  .header-btn {
    position: absolute; top: 11px; width: 108px; height: 37px;
    background: var(--sky); color: var(--white); font-size: 12px; font-weight: 600;
    display: flex; align-items: center; justify-content: center; letter-spacing: 0.3px;
  }
  .btn-intel { left: 832px; }
  .btn-planning { left: 954px; }
  .header-icon { position: absolute; top: 16px; }
  .icon-bell { left: 1083px; }
  .icon-share { left: 1124px; }

  .main-nav {
    position: absolute; left: 47px; top: 88px; display: flex; align-items: center;
    font-size: 13px; font-weight: 600;
  }
  .nav-item { white-space: nowrap; }
  .nav-item.is-active { color: var(--sky); font-weight: 500; }
  .nav-dot { width: 3px; height: 3px; border-radius: 50%; background: var(--sky); margin: 0 9px; }

  .property-search {
    position: absolute; left: 775px; top: 79px; width: 376px; height: 38px;
    border: 1px solid var(--frame); display: flex; align-items: center;
    padding: 0 16px; font-size: 11.5px; justify-content: space-between;
  }

  .menu {
    position: absolute; width: 163px; background: var(--sky); list-style: none;
    box-shadow: 0 3px 8px rgba(0, 40, 90, 0.18);
  }
  .menu li {
    height: 33.6px; display: flex; align-items: center; justify-content: space-between;
    padding: 0 11px; color: var(--white); font-size: 11px;
    border-top: 1px solid var(--sky-line);
  }
  .menu li:first-child { border-top: none; }
  .menu li.is-open { background: var(--navy); border-top-color: var(--navy); }
  .menu-primary { left: 49px; top: 124px; }
  .menu-primary::before {
    content: ""; position: absolute; left: 10px; top: -8px;
    border: 8px solid transparent; border-top: 0; border-bottom-color: var(--sky);
  }
  .menu-sub { left: 221px; top: 196px; }
</style>
</head>
<body>
  <header class="app-header">
    <div class="brand"><span class="brand-dot"></span><span class="brand-name">Silver Harbor Hotel &amp; Suites</span></div>
    <span class="welcome">Welcome Admin</span>
    <span class="today">Tuesday October 04.2017</span>
    <div class="header-btn btn-intel">INTEL</div>
    <div class="header-btn btn-planning">PLANNING</div>
    <svg class="header-icon icon-bell" width="28" height="26" viewBox="0 0 28 26" fill="none" stroke="#fff" stroke-width="1.3">
      <path d="M14 3c-4 0-6 3-6 7v5l-2 3h16l-2-3v-5c0-4-2-7-6-7z"/>
      <path d="M12 20a2 2 0 0 0 4 0"/>
      <path d="M4 8c-1 2-1 5 0 7M24 8c1 2 1 5 0 7"/>
    </svg>
    <svg class="header-icon icon-share" width="30" height="26" viewBox="0 0 30 26" fill="none" stroke="#fff" stroke-width="1.4" stroke-linejoin="round">
      <path d="M22 4v4c-8 0-13 4-14 11 3-4 7-5 14-5v4l6-7z"/>
      <path d="M18 19v4H3V9h4"/>
    </svg>
  </header>

  <nav class="main-nav">
    <span class="nav-item is-active">Admin</span><span class="nav-dot"></span>
    <span class="nav-item">Management</span><span class="nav-dot"></span>
    <span class="nav-item">Rooms Performance</span><span class="nav-dot"></span>
    <span class="nav-item">Revenue Summary</span><span class="nav-dot"></span>
    <span class="nav-item">Demand &amp; Risk</span><span class="nav-dot"></span>
    <span class="nav-item">Inventory Analysis</span><span class="nav-dot"></span>
    <span class="nav-item">Placeholder</span>
  </nav>

  <div class="property-search">
    <span>PROPERTY SEARCH</span>
    <svg width="14" height="14" viewBox="0 0 14 14" fill="none" stroke="#0d1a2b" stroke-width="1.2">
      <circle cx="6" cy="6" r="4.6"/><path d="M9.4 9.4L13 13"/>
    </svg>
  </div>

  <ul class="menu menu-primary">
    <li>Registration</li>
    <li>User Access</li>
    <li class="is-open">Setup
      <svg width="6" height="8" viewBox="0 0 6 8"><path d="M0 0l6 4-6 4z" fill="#fff"/></svg>
    </li>
    <li>Data Imoorts</li>
  </ul>

  <ul class="menu menu-sub">
    <li>Market Segments</li>
    <li>Banquet &amp; Catering</li>
    <li>Outlets / F&amp;B Service</li>
    <li>Other Income</li>
    <li>Impact Dates</li>
    <li>Inventory</li>
    <li>Geo/Location</li>
    <li>Distribution Channels</li>
  </ul>
</body>
</html>
```